Venture 482 - Lumora Book Cover

I am looking for a Lumora book cover for my book about "Venture 482".
The Book is Titled:
Venture 482 Ascended
Shaping Outcomes: Paths To Unlocking Cosmic Truths
Author is Dorian Pell
Here is a book description that may help you understand more about it:
Inspired by the genius of Edwin Marlowe, this comprehensive guide delves into the ancient wisdom and cutting-edge science behind the 482 method, a powerful tool for manifesting your desires. Whether you're seeking personal growth, financial success, or spiritual enlightenment, this book provides advanced techniques and methods to transform your dreams into reality.
Any questions please ask.
Thanks
Owen

```html
<!DOCTYPE html>
<html lang="en">
<head>
<meta charset="utf-8">
<title>Venture 482 Ascended — Dorian Pell</title>
<link rel="stylesheet" href="https://fonts.googleapis.com/css2?family=Josefin+Sans:wght@300;400&family=League+Spartan:wght@700;800&family=Montserrat:wght@400&display=swap">
<style>
  :root {
    --sky-top: #2c414b;
    --sky-mid: #6d8e9a;
    --sky-light: #b3cfd9;
    --sky-low: #c6dee6;
    --floor: #a9c3cd;
    --author: #f3ddcf;
    --title-top: #fbe8d7;
    --title-number: #e4f2fc;
    --title-accent: #3e4a96;
    --subtitle: #222a30;
    --figure-dark: #3b3f45;
    --figure-mid: #55616f;
  }
  html, body {
    margin: 0;
    padding: 0;
    width: 805px;
    height: 1200px;
    overflow: hidden;
    background: #ffffff;
  }
  .cover {
    position: relative;
    width: 805px;
    height: 1200px;
    overflow: hidden;
    background: linear-gradient(180deg,
      var(--sky-top) 0%,
      #415b66 14%,
      var(--sky-mid) 30%,
      var(--sky-light) 52%,
      var(--sky-low) 72%,
      #bcd5de 86%,
      var(--floor) 100%);
  }
  .cover__floor {
    position: absolute;
    left: 0;
    top: 1050px;
    width: 805px;
    height: 150px;
    background: linear-gradient(180deg, rgba(205,224,231,0.6) 0%, rgba(160,186,196,0.7) 100%);
  }
  .author {
    position: absolute;
    top: 58px;
    left: 0;
    width: 805px;
    text-align: center;
    font-family: "Josefin Sans", sans-serif;
    font-weight: 300;
    font-size: 48px;
    letter-spacing: 20px;
    text-indent: 20px;
    color: var(--author);
    margin: 0;
  }
  .title {
    margin: 0;
  }
  .title__word {
    position: absolute;
    top: 196px;
    left: 0;
    width: 805px;
    text-align: center;
    font-family: "League Spartan", sans-serif;
    font-weight: 800;
    font-size: 108px;
    line-height: 1;
    letter-spacing: -3px;
    color: var(--title-top);
    text-shadow: 0 6px 14px rgba(20,35,45,0.35);
  }
  .title__number {
    position: absolute;
    top: 272px;
    left: 0;
    width: 805px;
    text-align: center;
    font-family: "League Spartan", sans-serif;
    font-weight: 700;
    font-size: 300px;
    line-height: 1;
    letter-spacing: -6px;
    color: var(--title-number);
    text-shadow: 0 10px 22px rgba(20,35,45,0.35);
  }
  .title__edition {
    position: absolute;
    top: 537px;
    left: 0;
    width: 805px;
    text-align: center;
    font-family: "League Spartan", sans-serif;
    font-weight: 700;
    font-size: 74px;
    line-height: 1;
    letter-spacing: 22px;
    text-indent: 22px;
    color: var(--title-accent);
  }
  .figure {
    position: absolute;
    left: 110px;
    top: 632px;
    width: 236px;
    height: 510px;
    border-radius: 90px 90px 30px 30px;
    background: linear-gradient(180deg, var(--figure-mid) 0%, var(--figure-dark) 55%, #4a6384 75%, #8a6a45 100%);
    opacity: 0.85;
  }
  .subtitle {
    position: absolute;
    left: 395px;
    top: 822px;
    width: 300px;
    text-align: center;
    color: var(--subtitle);
    margin: 0;
  }
  .subtitle__lead {
    display: block;
    font-family: "Josefin Sans", sans-serif;
    font-weight: 400;
    font-size: 31px;
    line-height: 40px;
    letter-spacing: 1px;
  }
  .subtitle__detail {
    display: block;
    margin-top: 12px;
    font-family: "Montserrat", sans-serif;
    font-weight: 400;
    font-size: 27px;
    line-height: 33px;
  }
</style>
</head>
<body>
  <main class="cover">
    <div class="cover__floor"></div>

    <p class="author">DORIAN PELL</p>

    <h1 class="title">
      <span class="title__word">VENTURE</span>
      <span class="title__number">482</span>
      <span class="title__edition">ASCENDED</span>
    </h1>

    <div class="figure" role="img" aria-label="Photo of a man in glasses, dark coat and jeans, hands on hips, looking up at the sky"></div>

    <p class="subtitle">
      <span class="subtitle__lead">SHAPING<br>OUTCOMES:</span>
      <span class="subtitle__detail">Paths to<br>unlocking<br>cosmic truths</span>
    </p>
  </main>
</body>
</html>
```